Lifecoach needs website design based on a standard Wordpress theme

I need a website for my new lifecoaching business that can be easily implemented in Wordpress, it needs to be compatible with a standard Wordpress theme. So I can place the pictures, texts etc. in a standard theme of Wordpress.

I want the design to be a very good feeling and playfull one, based on my logo.

Target Market(s)

I will coach people to reach their goals and dreams in life.

Industry/Entity Type

Business

Requirements
Must have
• Can be easy implemented in Wordpress.
Nice to have
• Photo's of nature are nice.

```html
<!DOCTYPE html>
<html lang="en">
<head>
<meta charset="utf-8">
<title>Ruben Aldermoor Lifecoach</title>
<link href="https://fonts.googleapis.com/css2?family=Open+Sans:ital,wght@0,400;0,600;0,700;1,400&display=swap" rel="stylesheet">
<style>
:root{
  --navy:#0d4b7a;
  --accent:#1db0e6;
  --nav-top:#1b6aa3;
  --nav-bottom:#0b4a7c;
  --text:#666;
  --band:#f3f1f1;
  --card-line:#c9c9c9;
  --footer:#050505;
}
*{margin:0;padding:0;box-sizing:border-box}
html,body{width:1200px;height:2290px;overflow:hidden;background:#fff}
body{position:relative;font-family:"Open Sans",Arial,sans-serif;color:var(--text)}
.abs{position:absolute}

/* header */
.brand{left:134px;top:18px;display:flex;align-items:center;gap:14px}
.brand-mark{width:84px;height:84px;border-radius:50%;background:var(--accent)}
.brand-name{font-size:30px;font-weight:600;color:var(--navy);line-height:1.15}
.social{left:914px;top:24px;display:flex;gap:8px}
.social span{width:28px;height:28px;border-radius:50%;background:var(--accent);display:block}
.search{left:919px;top:75px;width:147px;height:21px;display:flex}
.search-field{flex:1;border:1px solid #ccc;border-radius:3px 0 0 3px;font-size:11px;color:#aaa;padding:2px 8px;background:#fafafa}
.search-btn{width:25px;background:var(--accent);border-radius:0 3px 3px 0}

/* nav */
.nav{left:0;top:134px;width:1200px;height:69px;background:linear-gradient(var(--nav-top),var(--nav-bottom))}
.nav a{position:absolute;top:24px;color:#fff;font-size:15px;text-decoration:none}

/* hero */
.hero{left:0;top:203px;width:1200px;height:389px;background:linear-gradient(180deg,#3c5a78 0%,#b9a25a 45%,#d9b24a 55%,#4d7c34 70%,#3d6b26 100%)}
.hero-text{left:160px;top:316px;width:400px;text-align:center;color:#fff;font-size:22px;line-height:1.75}
.hero-text em{font-style:italic}
.hero-text strong{font-size:29px;font-weight:700}
.hero-arrow{top:372px;width:24px;height:49px;background:rgba(220,220,220,.85)}
.hero-dots{left:568px;top:570px;display:flex;gap:8px}
.hero-dots span{width:11px;height:11px;border-radius:50%;background:#ccc}

/* content */
h2.section-title{position:absolute;left:139px;font-size:24px;font-weight:700;color:var(--navy)}
.body-copy{position:absolute;left:139px;width:922px;font-size:11.5px;line-height:20.6px;text-align:justify;color:var(--text)}
.program-img{top:1003px;width:455px;height:261px}
.program-title{width:455px;text-align:center;top:1276px;font-size:20px;color:var(--navy)}
.program-copy{top:1314px;width:430px;font-size:11.5px;line-height:20.6px;text-align:justify}
.more{font-size:12px;font-style:italic;color:#555}

.tools-band{left:0;top:1432px;width:1200px;height:353px;background:var(--band)}
.pager{display:flex;gap:4px}
.pager span{width:22px;height:27px;border:1px solid var(--card-line);background:#fff;font-size:15px;line-height:24px;text-align:center;color:#999}
.tool-card{top:1501px;width:208px;height:244px;border:1px solid var(--card-line);background:#fff;border-radius:2px}
.tool-card svg{position:absolute;left:56px;top:12px}
.tool-card h3{position:absolute;top:108px;width:100%;text-align:center;font-size:20px;font-weight:400;color:var(--navy)}
.tool-card p{position:absolute;left:10px;top:148px;width:186px;font-size:11.5px;line-height:20.6px;text-align:justify}
.tool-card .more{position:absolute;right:10px;top:214px}

.story-card{top:1875px;width:451px;height:145px;border:1px solid var(--card-line);border-radius:2px;background:#fff}
.story-photo{position:absolute;left:28px;top:14px;width:100px;height:116px}
.story-card h4{position:absolute;left:153px;top:12px;font-size:14px;font-weight:600;color:#555}
.story-card p{position:absolute;left:153px;top:38px;width:285px;font-size:11.5px;line-height:20.6px;text-align:justify}

/* footer */
.footer{left:0;top:2066px;width:1200px;height:224px;background:var(--footer);color:#fff}
.footer h5{position:absolute;font-size:22px;font-weight:600}
.footer p{position:absolute;font-size:11.5px;line-height:20px}
.map{left:133px;top:47px;width:279px;height:122px;background:linear-gradient(135deg,#e4e1d8,#d3d0c6)}
.news-field{left:800px;top:98px;width:254px;height:24px;background:#fff;border-radius:6px;color:#999;font-size:11px;padding:4px 10px}
.news-btn{left:800px;top:139px;width:96px;height:30px;background:var(--accent);border:1px solid #8ddcf7;border-radius:3px;font-size:17px;text-align:center;line-height:28px}
.footer-rule{left:131px;top:188px;width:938px;height:1px;background:#444}
.copyright{left:0;top:200px;width:1200px;text-align:center;font-size:11px}
</style>
</head>
<body>

<header>
  <div class="abs brand"><span class="brand-mark"></span><span class="brand-name">Ruben Aldermoor<br>Lifecoach</span></div>
  <div class="abs social"><span></span><span></span><span></span><span></span><span></span></div>
  <div class="abs search"><div class="search-field">Search</div><div class="search-btn"></div></div>
</header>

<nav class="abs nav">
  <a style="left:147px">Coaching Programs</a>
  <a style="left:328px">Blog</a>
  <a style="left:417px">Find a Coach</a>
  <a style="left:559px">Tools &amp; Support</a>
  <a style="left:722px">Success Stories</a>
  <a style="left:881px">About Us</a>
  <a style="left:1003px">Join Now</a>
</nav>

<section>
  <div class="abs hero" role="img" aria-label="Sunset over a grassy coast with a lone tree"></div>
  <div class="abs hero-text">We specialize in transition<br><em>life coaching for</em><br><strong>personal</strong> &amp; <strong>professional</strong><br>empowerment.</div>
  <div class="abs hero-arrow" style="left:0"></div>
  <div class="abs hero-arrow" style="right:0"></div>
  <div class="abs hero-dots"><span></span><span></span><span></span><span></span></div>
</section>

<main>
  <h2 class="section-title" style="top:645px">Welcome !!!</h2>
  <p class="body-copy" style="top:688px">Sed ut perspiciatis unde omnis iste natus error sit voluptatem accusantium doloremque laudantium, totam rem aperiam, eaque ipsa quae ab illo inventore veritatis et quasi architecto beatae vitae dicta sunt explicabo. Nemo enim ipsam voluptatem quia voluptas sit aspernatur aut odit aut fugit, sed quia consequuntur magni dolores eos qui ratione voluptatem sequi nesciunt. Neque porro quisquam est, qui dolorem ipsum quia dolor sit amet, consectetur, adipisci velit, sed quia non numquam eius modi tempora incidunt ut labore et dolore magnam aliquam quaerat voluptatem.</p>
  <p class="body-copy" style="top:776px">Ut enim ad minima veniam, quis nostrum exercitationem ullam corporis suscipit laboriosam, nisi ut aliquid ex ea commodi consequatur? Quis autem vel eum iure reprehenderit qui in ea voluptate velit esse quam nihil molestiae consequatur, vel illum qui dolorem eum fugiat quo voluptas nulla pariatur?</p>

  <h2 class="section-title" style="top:869px">Coaching Programs !!!</h2>
  <p class="body-copy" style="top:912px">Sed ut perspiciatis unde omnis iste natus error sit voluptatem accusantium doloremque laudantium, totam rem aperiam, eaque ipsa quae ab illo inventore veritatis et quasi architecto beatae vitae dicta sunt explicabo. Nemo enim ipsam voluptatem quia voluptas sit aspernatur aut odit aut fugit, sed quia consequuntur magni dolores eos qui ratione voluptatem sequi nesciunt. Neque porro quisquam est, qui dolorem ipsum quia dolor sit ame.</p>

  <div class="abs program-img" style="left:131px;background:linear-gradient(180deg,#5a9cc8,#c9dfe8 70%,#e8e3da)" role="img" aria-label="Woman raising her arms by the sea"></div>
  <div class="abs program-img" style="left:614px;background:linear-gradient(135deg,#8fb3cf,#3f4e64 55%,#e6e2dc)" role="img" aria-label="Smiling businesswoman with colleagues in an office"></div>
  <div class="abs program-title" style="left:131px">Personal Empowerment</div>
  <div class="abs program-title" style="left:614px">Professional Empowerment</div>
  <p class="abs program-copy" style="left:144px">Sed ut perspiciatis unde omnis iste natus error sit voluptatem accusantium doloremque laudantium, totam rem aperiam, eaque ipsa quae ab illo inventore veritatis et quasi architecto beatae..</p>
  <p class="abs program-copy" style="left:626px">Sed ut perspiciatis unde omnis iste natus error sit voluptatem accusantium doloremque laudantium, totam rem aperiam, eaque ipsa quae ab illo inventore veritatis et quasi architecto beatae..</p>
  <span class="abs more" style="left:510px;top:1380px">More Info...</span>
  <span class="abs more" style="left:992px;top:1380px">More Info...</span>

  <div class="abs tools-band"></div>
  <h2 class="section-title" style="top:1450px">Tools &amp; Support</h2>
  <div class="abs pager" style="left:1021px;top:1456px"><span>&lt;</span><span>&gt;</span></div>

  <div class="abs tool-card" style="left:131px">
    <svg width="96" height="90" viewBox="0 0 96 90"><ellipse cx="58" cy="28" rx="34" ry="24" fill="var(--accent)"/><path d="M70 48 L82 62 L62 51Z" fill="var(--accent)"/><ellipse cx="34" cy="52" rx="32" ry="22" fill="var(--accent)" stroke="#fff" stroke-width="3"/><path d="M18 70 L10 86 L30 72Z" fill="var(--accent)"/></svg>
    <h3>Forums</h3>
    <p>Sed ut perspiciatis unde omnis iste natus error sit voluptatem accusantium doloremque...</p>
    <span class="more">More Info...</span>
  </div>
  <div class="abs tool-card" style="left:374px">
    <svg width="96" height="90" viewBox="0 0 96 90"><circle cx="48" cy="44" r="42" fill="var(--accent)"/><text x="24" y="56" font-size="30" font-weight="700" fill="#fff" font-family="Open Sans,sans-serif">?</text><g fill="#fff"><rect x="46" y="20" width="26" height="9" rx="2"/><rect x="46" y="33" width="26" height="9" rx="2"/><rect x="46" y="46" width="26" height="9" rx="2"/><rect x="46" y="59" width="26" height="9" rx="2"/></g></svg>
    <h3>Forums</h3>
    <p>Sed ut perspiciatis unde omnis iste natus error sit voluptatem accusantium doloremque...</p>
    <span class="more">More Info...</span>
  </div>
  <div class="abs tool-card" style="left:618px">
    <svg width="96" height="90" viewBox="0 0 96 90"><circle cx="48" cy="44" r="39" fill="none" stroke="var(--accent)" stroke-width="6"/><path d="M36 22 L44 22 L47 34 L41 38 Q46 50 56 56 L60 50 L72 53 L72 61 Q62 70 46 60 Q30 48 28 32 Q30 24 36 22Z" fill="var(--accent)"/></svg>
    <h3>Forums</h3>
    <p>Sed ut perspiciatis unde omnis iste natus error sit voluptatem accusantium doloremque...</p>
    <span class="more">More Info...</span>
  </div>
  <div class="abs tool-card" style="left:860px">
    <svg width="96" height="90" viewBox="0 0 96 90"><path d="M28 8 H70 V78 H34 Q26 78 26 70 V14 Q26 8 32 8Z" fill="var(--accent)"/><path d="M34 70 H70 V84 H34 Q28 84 28 77 Q28 70 34 70Z" fill="#fff" stroke="var(--accent)" stroke-width="3"/></svg>
    <h3>Forums</h3>
    <p>Sed ut perspiciatis unde omnis iste natus error sit voluptatem accusantium doloremque...</p>
    <span class="more">More Info...</span>
  </div>

  <h2 class="section-title" style="top:1826px">Success Stories</h2>
  <div class="abs pager" style="left:1021px;top:1831px"><span>&lt;</span><span>&gt;</span></div>

  <div class="abs story-card" style="left:131px">
    <div class="story-photo" style="background:linear-gradient(#f0e2d2,#3a3a3a)" role="img" aria-label="Portrait of a smiling man in a suit"></div>
    <h4>Lorem ipsum</h4>
    <p>“adipiscing elit. Etiam quis placerat urna. Nulla nu adipiscing non ornardfe non, commodo non ipsum dolor sit. adipiscing elit. Etiam quis placerat urna. Nulla nu adipiscing.....”</p>
  </div>
  <div class="abs story-card" style="left:618px">
    <div class="story-photo" style="background:linear-gradient(#6b4a3a,#e9d3c4)" role="img" aria-label="Portrait of a smiling woman"></div>
    <h4>Lorem ipsum</h4>
    <p>“adipiscing elit. Etiam quis placerat urna. Nulla nu adipiscing non ornardfe non, commodo non ipsum dolor sit. adipiscing elit. Etiam quis placerat urna. Nulla nu adipiscing.....”</p>
  </div>
</main>

<footer class="abs footer">
  <h5 style="left:134px;top:14px">Location</h5>
  <div class="abs map" role="img" aria-label="Street map showing the office location"></div>
  <h5 style="left:548px;top:12px">Contact Us</h5>
  <p style="left:548px;top:43px">1.800.555.0142</p>
  <p style="left:548px;top:67px">help@aldermoorcoaching.example</p>
  <h5 style="left:800px;top:12px;font-weight:400">Our Newsletter</h5>
  <p style="left:800px;top:43px;width:270px">Stay ytuned as we give more updates and pffers through Ruben Aldermoor</p>
  <div class="abs news-field">Enter your email id:</div>
  <div class="abs news-btn">SUBMIT</div>
  <div class="abs footer-rule"></div>
  <div class="abs copyright">©2014 Ruben Aldermoor | Privacy Policy | Terms &amp; Conditions</div>
</footer>

</body>
</html>
```